Salon and Spa Distributor Business Card

Need a business card. We are are distributor in the salon and spa industry. We identify with natural beauty. Need a card with:
Company Name: Petal Quarry"
Title: "President & CEO"
Address
Company Phone number
email
website
Tag Line:" The Professional Salon Source"

Industry/Entity Type

Business

Contact Information for Business Card

Name: Dov Strommen
Title: "President & CEO"
Address: 31 Harlow Ln, Bexmoor, NJ 07813
Company Phone number: 800-463-5918
email: dovstrommen@petalquarry.example
website: www.petalquarry.example

Requirements
Should not have
• No black backgrounds

```html
<!DOCTYPE html>
<html lang="en">
<head>
<meta charset="utf-8">
<title>Petal Quarry Business Card</title>
<link rel="stylesheet" href="https://fonts.googleapis.com/css2?family=Questrial&display=swap">
<style>
  :root {
    --page-bg: #e9e7e4;
    --card-white: #ffffff;
    --brand-green: #1f9a3a;
    --brand-green-deep: #0f7a2c;
    --brand-green-dark: #0b5e22;
    --brand-green-light: #4cc34a;
    --back-mark: #2f8a43;
    --ink: #3a3a3a;
    --ink-soft: #6a6a6a;
  }
  * { box-sizing: border-box; margin: 0; padding: 0; }
  html, body { width: 1200px; height: 716px; overflow: hidden; }
  body {
    background: var(--page-bg);
    font-family: "Questrial", "Century Gothic", sans-serif;
    position: relative;
  }
  .card {
    position: absolute;
    top: 203px;
    width: 540px;
    height: 309px;
    overflow: hidden;
    box-shadow: 0 6px 18px rgba(0,0,0,0.18);
  }
  .card-back { left: 40px; background: var(--brand-green-dark); }
  .card-front { left: 620px; background: var(--card-white); }

  .back-mark {
    position: absolute;
    inset: 0;
    display: flex; align-items: center; justify-content: center; gap: 12px;
    font-size: 34px;
    color: var(--back-mark);
  }
  .back-mark .dot {
    width: 22px; height: 22px; border-radius: 50%;
    background: var(--back-mark);
  }

  .header-bar {
    position: absolute;
    left: 18px; top: 18px;
    width: 11px; height: 50px;
    background: var(--brand-green);
  }
  .company-name {
    position: absolute;
    left: 38px; top: 14px;
    font-size: 25px;
    font-weight: 400;
    color: var(--brand-green-deep);
    letter-spacing: 0.2px;
    white-space: nowrap;
  }
  .person {
    position: absolute;
    left: 40px; top: 46px;
    font-size: 11px;
    color: var(--ink-soft);
    line-height: 13px;
    white-space: nowrap;
  }
  .person .person-name { color: var(--ink); }

  .contact-list {
    position: absolute;
    left: 30px; top: 172px;
    list-style: none;
    font-size: 13px;
    color: var(--ink);
    line-height: 17px;
    white-space: nowrap;
  }
  .contact-list li { display: flex; align-items: center; gap: 8px; }
  .contact-list svg { width: 11px; height: 11px; fill: var(--brand-green-deep); flex: none; }

  .logo-name {
    position: absolute;
    left: 330px; top: 132px;
    display: flex; align-items: center; gap: 10px;
    font-size: 22px;
    color: var(--brand-green);
    white-space: nowrap;
  }
  .logo-name .dot {
    width: 16px; height: 16px; border-radius: 50%;
    background: var(--brand-green-light);
    flex: none;
  }

  .bottom-rule {
    position: absolute;
    left: 0; bottom: 40px;
    width: 300px; height: 4px;
    background: var(--brand-green);
  }
  .tagline-tab {
    position: absolute;
    right: 0; bottom: 0;
    width: 300px; height: 48px;
    background: var(--brand-green-deep);
    clip-path: polygon(10% 0, 100% 0, 100% 100%, 0 100%);
    display: flex; align-items: center; justify-content: flex-end;
    padding-right: 24px;
    color: var(--card-white);
    font-size: 14px;
    white-space: nowrap;
  }
</style>
</head>
<body>
  <section class="card card-back">
    <div class="back-mark"><span class="dot"></span><span>Petal Quarry</span></div>
  </section>

  <section class="card card-front">
    <div class="header-bar"></div>
    <h1 class="company-name">Petal Quarry</h1>
    <p class="person"><span class="person-name">Dov Strommen</span> · President &amp; CEO</p>

    <ul class="contact-list">
      <li>
        <svg viewBox="0 0 24 24" aria-hidden="true"><path d="M6.6 10.8a15 15 0 0 0 6.6 6.6l2.2-2.2a1 1 0 0 1 1-.25 11.4 11.4 0 0 0 3.6.57 1 1 0 0 1 1 1V20a1 1 0 0 1-1 1A17 17 0 0 1 3 4a1 1 0 0 1 1-1h3.5a1 1 0 0 1 1 1c0 1.25.2 2.45.57 3.57a1 1 0 0 1-.25 1z"/></svg>
        <span>800-463-5918</span>
      </li>
      <li>
        <svg viewBox="0 0 24 24" aria-hidden="true"><path d="M2 5h20v14H2z M2 5l10 8 10-8" fill="none" stroke="#0f7a2c" stroke-width="2.5"/></svg>
        <span>dovstrommen@petalquarry.example</span>
      </li>
      <li>
        <svg viewBox="0 0 24 24" aria-hidden="true"><circle cx="12" cy="12" r="10" fill="none" stroke="#0f7a2c" stroke-width="2.5"/><path d="M2 12h20M12 2c3 3 3 17 0 20M12 2c-3 3-3 17 0 20" fill="none" stroke="#0f7a2c" stroke-width="2"/></svg>
        <span>www.petalquarry.example</span>
      </li>
      <li><span>31 Harlow Ln, Bexmoor, NJ 07813</span></li>
    </ul>

    <div class="logo-name"><span class="dot"></span><span>Petal Quarry</span></div>

    <div class="bottom-rule"></div>
    <div class="tagline-tab">The Professional Salon Source</div>
  </section>
</body>
</html>
```